Help me make landing pages for my web application that are mobile friendly

I need to make 2 mobile friendly landing pages for an application. The 2 pages will be related. First I need a home page and then I need a working page. I do not want to change the color scheme or logos. Just layout and design.

```html
<!DOCTYPE html>
<html lang="en">
<head>
<meta charset="utf-8">
<title>ShiftCover — Assignments &amp; Opening</title>
<link rel="stylesheet" href="https://fonts.googleapis.com/css2?family=Kumbh+Sans:wght@400;500;600;700&display=swap">
<style>
:root{
  --purple:#6a4fb3;
  --teal:#2aa8d8;
  --navy:#0a5fc0;
  --green:#3a9a2a;
  --red:#e8001c;
  --ink:#1d1d1f;
  --muted:#444;
  --panel:#f1f1f2;
  --line:#dcdcdf;
  --backdrop:#a4a4a6;
  --white:#fff;
}
*{box-sizing:border-box;margin:0;padding:0}
html,body{width:1200px;height:3003px;overflow:hidden}
body{background:var(--backdrop);font-family:"Kumbh Sans",sans-serif;color:var(--ink);position:relative}
.screen{position:absolute;top:0;background:var(--white);transform-origin:0 0;transform:scale(1.3636)}
.screen--home{left:0;width:414px;height:1883px}
.screen--work{left:633px;width:416px;height:2202px}
.abs{position:absolute}
.brand{position:absolute;top:60px;left:0;right:0;display:flex;justify-content:center;align-items:center;gap:8px;font-size:31px;font-weight:600;color:var(--purple)}
.brand-dot{width:22px;height:22px;border-radius:50%;background:var(--teal)}
.menu{position:absolute;top:68px;left:25px}
.home{position:absolute;top:67px;width:26px;height:26px;border-radius:50%;background:var(--teal);display:flex;align-items:center;justify-content:center}
.tabs{position:absolute;top:115px;left:20px;right:20px;height:40px;border-bottom:1px solid var(--line);display:flex;align-items:flex-start;gap:16px;font-size:15px}
.tab{padding:8px 0}
.tab--on{background:var(--purple);color:#fff;border-radius:3px;padding:8px 10px}
.section{position:absolute;background:var(--panel)}
.section-title{position:absolute;font-size:20px;font-weight:700;letter-spacing:.3px}
.card{position:absolute;left:13px;width:348px;height:229px;background:#fff;border:1px solid var(--line);border-radius:8px}
.card h3{position:absolute;left:16px;top:10px;font-size:18px;font-weight:600}
.edit{position:absolute;right:18px;top:12px}
.avatar{position:absolute;left:10px;top:45px;width:54px;height:54px;border-radius:50%;border:2px solid var(--teal)}
.avatar-fill{position:absolute;inset:3px;border-radius:50%;background:linear-gradient(160deg,#c9a98f,#5b4a44)}
.avatar--initials{display:flex;align-items:center;justify-content:center;color:var(--teal);font-size:18px;font-weight:600}
.ok{position:absolute;right:-2px;bottom:-2px;width:13px;height:13px;border-radius:50%;background:var(--green);border:1.5px solid #fff}
.who{position:absolute;left:80px;top:52px}
.who--flat{left:18px;top:42px}
.who b{display:block;color:var(--teal);font-size:19px;font-weight:500}
.who span{display:block;color:var(--teal);font-size:15px;margin-top:1px}
.row{position:absolute;left:18px;display:flex;align-items:center;gap:8px;font-size:15px;font-weight:500}
.row svg{flex:none}
.pill{color:#fff;border-radius:12px;padding:2px 10px;font-size:15px;font-weight:600}
.pill--done{background:var(--navy)}.pill--active{background:var(--green)}.pill--cancel{background:var(--red)}
.field-label{position:absolute;left:16px;font-size:19px;font-weight:600}
.field-val{position:absolute;left:16px;font-size:15px}
.box{position:absolute;background:#fff;border:1px solid var(--line);border-radius:4px}
.btn{position:absolute;height:37px;border-radius:19px;color:#fff;font-weight:600;font-size:15px;display:flex;align-items:center;justify-content:center;gap:8px}
.btn--teal{background:var(--teal)}.btn--purple{background:var(--purple)}
.input{position:absolute;left:38px;width:340px;height:37px;background:#fff;border:1px solid var(--line);border-radius:4px;display:flex;align-items:center;padding:0 14px;font-size:17px;justify-content:space-between}
.check{width:21px;height:21px;border:1px solid #aaa;border-radius:3px;background:#fff}
.lbl{position:absolute;left:46px;font-size:17px;font-weight:600}
</style>
</head>
<body>
<svg width="0" height="0" style="position:absolute">
  <symbol id="pin" viewBox="0 0 12 16"><path d="M6 0a6 6 0 0 0-6 6c0 4.5 6 10 6 10s6-5.5 6-10a6 6 0 0 0-6-6zm0 8.3A2.3 2.3 0 1 1 6 3.7a2.3 2.3 0 0 1 0 4.6z" fill="#1d1d1f"/></symbol>
  <symbol id="bell" viewBox="0 0 14 16"><path d="M7 0c.8 0 1.3.6 1.3 1.3v.4A4.8 4.8 0 0 1 12 6.4V10l2 2.5v1H0v-1L2 10V6.4a4.8 4.8 0 0 1 3.7-4.7v-.4C5.7.6 6.2 0 7 0zM5 14.3h4a2 2 0 0 1-4 0z" fill="#1d1d1f"/></symbol>
  <symbol id="clock" viewBox="0 0 16 16"><circle cx="8" cy="8" r="8" fill="currentColor"/><path d="M8 3.5V8l3 2" stroke="#fff" stroke-width="1.8" fill="none" stroke-linecap="round"/></symbol>
  <symbol id="pencil" viewBox="0 0 16 16"><path d="M0 12.5V16h3.5L13.8 5.7l-3.5-3.5zM15.7 3.8a1 1 0 0 0 0-1.4L13.6.3a1 1 0 0 0-1.4 0l-1.6 1.6 3.5 3.5z" fill="#2aa8d8"/></symbol>
  <symbol id="cal" viewBox="0 0 16 16"><rect x="1" y="3" width="14" height="12" rx="2" fill="#2aa8d8"/><rect x="4" y="0" width="2" height="4" fill="#2aa8d8"/><rect x="10" y="0" width="2" height="4" fill="#2aa8d8"/><rect x="1" y="6" width="14" height="1.5" fill="#fff"/></symbol>
  <symbol id="menu" viewBox="0 0 20 18"><rect y="1" width="20" height="3" rx="1.5" fill="#2aa8d8"/><rect y="7.5" width="16" height="3" rx="1.5" fill="#2aa8d8"/><rect y="14" width="12" height="3" rx="1.5" fill="#2aa8d8"/></symbol>
  <symbol id="house" viewBox="0 0 16 16"><path d="M8 2 1.5 8H4v6h3v-4h2v4h3V8h2.5z" fill="none" stroke="#fff" stroke-width="1.6" stroke-linejoin="round"/></symbol>
</svg>

<!-- Home: My Assignments -->
<main class="screen screen--home">
  <svg class="menu" width="20" height="18"><use href="#menu"/></svg>
  <div class="brand"><span class="brand-dot"></span>ShiftCover</div>
  <div class="home" style="left:359px"><svg width="16" height="16"><use href="#house"/></svg></div>
  <nav class="tabs"><span class="tab tab--on">My Assignments</span><span class="tab">Available Openings</span><span class="tab">Support</span></nav>

  <section class="section" style="left:20px;top:167px;width:375px;height:1513px">
    <div class="abs" style="left:0;top:0;right:0;height:42px;border-bottom:1px solid var(--line)"></div>
    <h2 class="section-title" style="left:16px;top:9px">My Assignments</h2>
    <div class="abs" style="right:14px;top:10px;width:22px;height:22px;border-radius:50%;background:var(--purple);color:#fff;font-size:15px;font-weight:700;display:flex;align-items:center;justify-content:center">?</div>

    <article class="card" style="top:52px">
      <h3>Subbing For:</h3><svg class="edit" width="16" height="16"><use href="#pencil"/></svg>
      <div class="avatar"><div class="avatar-fill" role="img" aria-label="Profile photo of Dana Whitfield"></div><span class="ok"></span></div>
      <div class="who"><b>Dana Whitfield</b><span>Teacher</span></div>
      <div class="row" style="top:120px"><svg width="12" height="16"><use href="#pin"/></svg>Location : MRES</div>
      <div class="row" style="top:149px"><svg width="14" height="16"><use href="#bell"/></svg>Status : <span class="pill pill--done">Complete</span></div>
      <div class="row" style="top:183px;color:var(--ink)"><svg width="16" height="16" style="color:#1d1d1f"><use href="#clock"/></svg>Time Slots : &nbsp;09/02-09/02 (1h 0m)</div>
    </article>

    <article class="card" style="top:293px">
      <h3>Subbing For:</h3><svg class="edit" width="16" height="16"><use href="#pencil"/></svg>
      <div class="who who--flat"><b>Extra duty</b><span>Teacher</span></div>
      <div class="row" style="top:100px"><svg width="12" height="16"><use href="#pin"/></svg>Location : MRES</div>
      <div class="row" style="top:129px"><svg width="14" height="16"><use href="#bell"/></svg>Status : <span class="pill pill--done">Complete</span></div>
      <div class="row" style="top:163px"><svg width="16" height="16" style="color:#1d1d1f"><use href="#clock"/></svg>Time Slots : &nbsp;07/10 - 07/11/1h 20m)</div>
    </article>

    <article class="card" style="top:533px">
      <h3>Subbing For:</h3><svg class="edit" width="16" height="16"><use href="#pencil"/></svg>
      <div class="avatar avatar--initials">OC<span class="ok"></span></div>
      <div class="who"><b>Owen Carter</b><span>Teacher</span></div>
      <div class="row" style="top:120px"><svg width="12" height="16"><use href="#pin"/></svg>Location : MRES</div>
      <div class="row" style="top:149px"><svg width="14" height="16"><use href="#bell"/></svg>Status : <span class="pill pill--done">Complete</span></div>
      <div class="row" style="top:183px"><svg width="16" height="16" style="color:#1d1d1f"><use href="#clock"/></svg>Time Slots : &nbsp;09/02-09/02 (1h 0m)</div>
    </article>

    <article class="card" style="top:774px">
      <h3>Subbing For:</h3><svg class="edit" width="16" height="16"><use href="#pencil"/></svg>
      <div class="avatar"><div class="avatar-fill" role="img" aria-label="Profile photo of Reid Halvorsen"></div><span class="ok"></span></div>
      <div class="who"><b>Reid Halvorsen</b><span>Administrator</span></div>
      <div class="row" style="top:120px"><svg width="12" height="16"><use href="#pin"/></svg>Location : MRES</div>
      <div class="row" style="top:149px"><svg width="14" height="16"><use href="#bell"/></svg>Status : <span class="pill pill--active">Active</span></div>
      <div class="row" style="top:183px"><svg width="16" height="16" style="color:#1d1d1f"><use href="#clock"/></svg>Time Slots : &nbsp;07/26 - 08/07 (14h 15m)</div>
    </article>

    <article class="card" style="top:1015px">
      <h3>Subbing For:</h3><svg class="edit" width="16" height="16"><use href="#pencil"/></svg>
      <div class="avatar"><div class="avatar-fill" role="img" aria-label="Profile photo of Priya Lanford"></div><span class="ok"></span></div>
      <div class="who"><b>Priya Lanford</b><span>Teacher</span></div>
      <div class="row" style="top:120px"><svg width="12" height="16"><use href="#pin"/></svg>Location : MRES</div>
      <div class="row" style="top:149px"><svg width="14" height="16"><use href="#bell"/></svg>Status : <span class="pill pill--cancel">Canceled</span></div>
      <div class="row" style="top:183px"><svg width="16" height="16" style="color:#1d1d1f"><use href="#clock"/></svg>Time Slots : &nbsp;07/31 07/31 (9h 0m)</div>
    </article>

    <article class="card" style="top:1257px">
      <h3>Subbing For:</h3><svg class="edit" width="16" height="16"><use href="#pencil"/></svg>
      <div class="avatar"><div class="avatar-fill" role="img" aria-label="Profile photo of Marcus Ellery"></div><span class="ok"></span></div>
      <div class="who"><b>Marcus Ellery</b><span>Teacher</span></div>
      <div class="row" style="top:120px"><svg width="12" height="16"><use href="#pin"/></svg>Location : MRES</div>
      <div class="row" style="top:149px"><svg width="14" height="16"><use href="#bell"/></svg>Status : <span class="pill pill--active">Active</span></div>
      <div class="row" style="top:183px"><svg width="16" height="16" style="color:#1d1d1f"><use href="#clock"/></svg>Time Slots : &nbsp;07/31 07/31 (9h 0m)</div>
    </article>
  </section>
</main>

<!-- Working page: Opening Information -->
<main class="screen screen--work">
  <svg class="menu" width="20" height="18"><use href="#menu"/></svg>
  <div class="brand"><span class="brand-dot"></span>ShiftCover</div>
  <div class="home" style="left:359px"><svg width="16" height="16"><use href="#house"/></svg></div>

  <section class="section" style="left:20px;top:104px;width:375px;height:1894px">
    <div class="abs" style="left:0;right:0;top:0;height:46px;border-bottom:1px solid var(--line)"></div>
    <h2 class="section-title" style="left:16px;top:12px">Opening Information</h2>

    <div class="box" style="left:13px;top:58px;width:348px;height:858px;border-radius:8px">
      <svg class="abs" style="right:14px;top:12px" width="16" height="16"><use href="#pencil"/></svg>
      <div class="field-label" style="top:10px">Summary</div><div class="field-val" style="top:42px">Testing-test</div>
      <div class="field-label" style="top:77px">Location</div><div class="field-val" style="top:109px">Maple Ridge Elementary School</div>
      <div class="field-label" style="top:145px">Type</div><div class="field-val" style="top:177px">Vacancy</div>
      <div class="field-label" style="top:213px">Regular Staff</div><div class="field-val" style="top:245px">Owen Carter</div>
      <svg class="abs" style="right:24px;top:245px" width="14" height="10"><path d="M1 2l6 6 6-6" stroke="#333" stroke-width="1.8" fill="none"/></svg>
      <div class="field-label" style="top:284px">Assignment Category</div><div class="field-val" style="top:316px">Teacher</div>
      <div class="field-label" style="top:355px">Department</div>
      <div class="field-label" style="top:426px">Description</div>
      <div class="abs" style="left:15px;top:457px;width:316px;height:116px;background:var(--panel);border-radius:6px;padding:13px 14px;font-size:15px;line-height:1.3">Lorem ipsum dolor sit amet, consectetur adipiscing elit, sed do eiusmod tempor incididunt ut labore et dolore magna aliqua.</div>
      <div class="abs" style="left:15px;top:588px;width:316px;height:246px;background:var(--panel);border-radius:6px">
        <div class="abs" style="left:17px;top:12px;font-size:18px;font-weight:600">Comments</div>
        <div class="box" style="left:12px;top:44px;width:292px;height:78px;border:none;padding:14px 13px;font-size:15px;color:var(--muted)">Write a comment or upload a file...</div>
        <div class="box" style="left:12px;top:132px;width:292px;height:45px;border:none;padding:13px 13px;font-size:15px;color:var(--muted)">No comments or files uploaded</div>
        <div class="btn btn--teal" style="left:16px;top:190px;width:101px"><svg width="17" height="15" viewBox="0 0 17 15"><path d="M0 6.5 17 0l-4 15-5-5L14 3 5 9z" fill="#fff"/></svg>POST</div>
        <div class="btn btn--purple" style="left:122px;top:190px;width:122px"><svg width="14" height="16" viewBox="0 0 14 16"><path d="M11 7 6 12a2.5 2.5 0 0 1-3.5-3.5L8 3a1.6 1.6 0 0 1 2.3 2.3L5 10.6" stroke="#fff" stroke-width="1.6" fill="none" stroke-linecap="round"/></svg>UPLOAD</div>
      </div>
    </div>

    <div class="abs" style="left:0;right:0;top:985px;height:1px;background:var(--line)"></div>
    <h2 class="section-title" style="left:33px;top:946px">Additional Details</h2>
    <div class="box" style="left:13px;top:1001px;width:348px;height:118px;border-radius:8px">
      <div class="abs" style="left:20px;top:18px;font-size:19px;font-weight:500">Parking Spot</div>
      <div class="box" style="left:16px;top:54px;width:312px;height:37px;border-color:#bbb"></div>
    </div>

    <div class="abs" style="left:0;right:0;top:1186px;height:1px;background:var(--line)"></div>
    <h2 class="section-title" style="left:33px;top:1147px">Time Slots</h2>
    <div class="box" style="left:26px;top:1201px;width:140px;height:37px;display:flex;align-items:center;justify-content:center;font-size:17px">Accept</div>
    <div class="box" style="left:177px;top:1201px;width:140px;height:37px;display:flex;align-items:center;justify-content:center;font-size:17px">Withdraw</div>

    <div class="input" style="left:18px;top:1254px;justify-content:flex-start;gap:18px;padding-left:10px;font-weight:500"><span class="check"></span>Date</div>
    <div class="input" style="left:18px;top:1296px;justify-content:flex-start;gap:18px;padding-left:10px"><span class="check"></span>3/19/2026<svg style="margin-left:auto" width="16" height="16"><use href="#cal"/></svg></div>
    <div class="lbl" style="left:26px;top:1351px">From :</div>
    <div class="input" style="left:18px;top:1379px">9:30 AM<svg width="16" height="16" style="color:var(--teal)"><use href="#clock"/></svg></div>
    <div class="lbl" style="left:26px;top:1426px">To :</div>
    <div class="input" style="left:18px;top:1454px">12:30 PM<svg width="16" height="16" style="color:var(--teal)"><use href="#clock"/></svg></div>
    <div class="abs" style="left:26px;top:1517px;font-size:16px"><b style="font-weight:600">Current Assignment :</b>&nbsp; No Assignment</div>
    <div class="abs" style="left:26px;top:1558px;font-size:16px"><b style="font-weight:600">Status :</b>&nbsp; Active</div>
    <div class="input" style="left:18px;top:1607px;justify-content:flex-start;gap:18px;padding-left:10px"><span class="check"></span>3/19/2026<svg style="margin-left:auto" width="16" height="16"><use href="#cal"/></svg></div>
    <div class="lbl" style="left:26px;top:1662px">From :</div>
    <div class="input" style="left:18px;top:1690px">2:30 PM<svg width="16" height="16" style="color:var(--teal)"><use href="#clock"/></svg></div>
    <div class="lbl" style="left:26px;top:1737px">To :</div>
    <div class="input" style="left:18px;top:1765px">4:00 PM<svg width="16" height="16" style="color:var(--teal)"><use href="#clock"/></svg></div>
    <div class="btn btn--teal" style="left:74px;top:1821px;width:101px">SAVE</div>
    <div class="btn btn--purple" style="left:180px;top:1821px;width:122px">CLOSE</div>
  </section>
</main>
</body>
</html>
```